Bold, Modern, Clean "Kestrelwaymassage.com" website

Why we stand out?
We are a male and female mobile massage team. Our names are Paul and Lina. 
Kestrel Way is a Seattle based mobile massage service. Our massage is offered to the community with a goal of facilitating balance within each individual. We specialize in integrated Pain management, and sports/medical massage therapy. Every client's first assessment is attended by our male and female massage therapist team. Depending on the goals identified for an individual determines which therapist will be assigned to provide treatment, if not both.

Our passion...
Here at Kestrel Way, we have a great passion for Postural Resoration and how it is integrated into an individual's Massage treatment. We pride ourselves in being natural facilitators of healing, which takes the ego of the therapist out of the client's healing process. We strive to deliver the best massage possible by including modalities such as Neuromuscular, Myofascial release, spontaneous muscle release, postural restoration, orthopedic, and medical massage.

Our education...

We are both Graduates of Venmora, school of massage therapy. We have continuing education in medical massage, myofacial release, trigger point therapy, postural restoration, anatomy, and spontaneous muscle release. Lina is also a Certified Yoga Instructor, which amplifies her experience with flexibility and strength as it pertains to each individual. Paul's passion is Massage, stretching, and strength training to encourage postural restoration and realignment.

Our rates-

Our rates are $75/ 60 minutes, $95/ 90 minutes, and $120/ 120 minutes.

Education-
Both Lina and I worked as behavioral health professionals that specialized in life skills mentoring for youth who had experienced different types of trauma. This led us both to want to help others in a different environment, where individuals can be empowered to take responsibility over their own healing. To us, massage is a type of manipulation physical therapy, that encourages healing on many levels.

Advice to any massage client-
The most important thing to 'us', as Licenced providers is to get you on to our table to show you our skills. But a good therapist never forgets that it's not about what we do for you, but what we can facilitate for you. Your health and healing has nothing to do with us. It is yours, not ours. Identify what your goals are with any Therapist, and know what the end looks like. Progress should be tangible, such as range of motion, and decreased pain.

Lina and Paul at Kestrel Way are awesome! I recently had open heart surgery, and Lina worked on me to increase my range of motion while helping with the pinched nerve from my arm being in the same position for so long during my surgery. My wife drives a lot for work, and Paul has helped decrease her neck and lower back pain immensely. They are seriously the best therapists I have ever worked with. I would recommend them to anyone who needs anything from stress relief to a medical massage treatment. They are professional, up beat, easy going, and always on time. And, I love that they meet us where ever we like! We did a staycation recently, where they came to our hotel to give us relaxation massages. Although usually they come to our home, where we focus on pain related issues. We will continue to work with them for a long, long time.

Target Market(s)

Mobile massage therapy clients

Industry/Entity Type

Massage Therapy

Coding

Coded - Design and coding required

Number of Pages Required

1 page

Font styles to use
Serif
Sans Serif

Requirements
Must have
• Please add or remove any information that would help the presentation of our website. Our logo is posted below, please include into the website.
• Please include a contact field that includes, kestrelwaymassage@fernmail.net,
• (206) 555-0148
• We have also included our own stock photos, as well as a photo of Paul and Lina. Please include a cropped photo of both massage therapists.

```html
<!DOCTYPE html>
<html lang="en">
<head>
<meta charset="utf-8">
<title>Kestrel Way Mobile Massage</title>
<link rel="stylesheet" href="https://fonts.googleapis.com/css2?family=Open+Sans:wght@300;400;600&family=Noto+Serif&display=swap">
<style>
:root{
  --blue:#0a95cc;
  --blue-dark:#0b7fb0;
  --ink:#1e1e1e;
  --grey:#8a8f94;
  --soft:#f3f5f7;
  --line:#e3e6e9;
  --night:#1f1a17;
  --white:#ffffff;
}
*{box-sizing:border-box;margin:0;padding:0}
html,body{width:1200px;height:2707px;overflow:hidden;background:var(--white)}
body{position:relative;font-family:"Open Sans",Arial,sans-serif;color:var(--ink)}
.abs{position:absolute}
.center{left:0;width:1200px;text-align:center}
.accent{color:var(--blue)}
.section-title{font-weight:400;font-size:35px;letter-spacing:.3px}
.rule{position:absolute;left:544px;width:112px;height:2px;background:var(--blue)}

/* top bar */
.topbar{top:0;left:0;width:1200px;height:49px;background:var(--blue);color:var(--white);font-size:12px}
.topbar .booking{left:866px;top:16px}
.topbar .phone-icon{left:952px;top:12px}
.topbar .phone{left:990px;top:16px}

/* nav */
.navbar{top:49px;left:0;width:1200px;height:81px;background:var(--white)}
.nav-item{top:34px;font-size:12.5px;color:#333}
.nav-active{left:505px;top:0;width:67px;height:81px;background:#f2f6f8}
.nav-active + .nav-item{color:var(--blue)}
.brand{left:128px;top:18px;width:144px;height:144px;border-radius:50%;background:var(--white);z-index:5;display:flex;align-items:center;justify-content:center}
.brand-name{font-weight:600;font-size:22px;color:#1b3f7a;text-align:center;line-height:1.1;width:100px}

/* hero */
.hero{top:130px;left:0;width:1200px;height:451px;background:linear-gradient(100deg,#6b3d26 0%,#b06c45 35%,#8a5234 60%,#3b2419 100%)}
.hero-shade{top:130px;left:0;width:1200px;height:451px;background:rgba(0,0,0,.25)}
.hero-title{top:252px;font-size:35px;font-weight:300;color:var(--white)}
.hero-title b{font-weight:600;color:var(--blue)}
.hero-sub{top:304px;font-family:"Noto Serif",Georgia,serif;font-size:21px;line-height:28px;color:var(--white)}
.btn-book{left:507px;top:392px;width:184px;height:45px;border-radius:23px;background:var(--blue);color:var(--white);font-size:13px;font-weight:600;text-align:center;line-height:45px}
.dots{top:538px;left:572px}
.dot{display:inline-block;width:5px;height:5px;border-radius:50%;background:rgba(255,255,255,.45);margin:0 8px}
.dot.on{background:var(--white)}

/* welcome */
.welcome-title{top:630px}
.welcome-text{top:727px;left:132px;width:936px;font-size:12px;line-height:19px;color:var(--grey);text-align:center}
.btn-small{left:554px;top:816px;width:90px;height:29px;background:var(--blue);color:var(--white);font-size:11.5px;text-align:center;line-height:29px;border-radius:2px}

/* massages */
.massage-band{top:910px;left:0;width:1200px;height:440px;background:var(--soft)}
.card{width:300px;text-align:center}
.card-icon{margin:0 auto;width:88px;height:88px}
.card h3{margin-top:26px;font-weight:400;font-size:20px;color:var(--blue)}
.card p{margin-top:18px;font-size:11.5px;line-height:19px;color:var(--grey)}
.card .more{margin-top:14px;font-size:11px;color:var(--blue)}

/* why */
.why{top:1350px;left:0;width:1200px;height:451px;background:linear-gradient(180deg,#0f9bd2 0%,#0a8dc5 50%,#0b7fb8 100%)}
.why-photo{top:1350px;left:0;width:760px;height:451px;background:radial-gradient(ellipse at 35% 55%,rgba(120,200,235,.35),rgba(10,140,200,0) 70%)}
.why-title{top:1405px;color:var(--white)}
.why .rule{background:var(--white)}
.reason{width:300px;color:var(--white)}
.reason h4{margin-top:14px;font-weight:400;font-size:13px;letter-spacing:.3px}
.reason p{margin-top:12px;font-size:11.5px;line-height:19px;color:#e2f3fb}
.reason .more{margin-top:12px;font-size:11px}

/* testimonials */
.testi-title{top:1834px}
.avatar{top:1937px;width:80px;height:80px;border-radius:50%;background:linear-gradient(160deg,#c8a48a,#7d5a44)}
.avatar.active{box-shadow:0 0 0 4px var(--white),0 0 0 6px var(--blue)}
.quote-text{top:2070px;left:140px;width:920px;font-size:11.5px;line-height:20px;color:var(--grey);text-align:center}
.quote-name{top:2117px;font-size:12px;font-style:italic;color:var(--blue)}

/* contact */
.contact{top:2190px;left:0;width:1200px;height:517px;background:radial-gradient(ellipse at 50% 55%,#3e332c 0%,#221c18 60%,#141110 100%)}
.contact-title{top:2221px;color:var(--white)}
.contact .rule{top:2292px}
.touch{left:134px;top:2355px;font-size:19px;color:var(--white)}
.touch-text{left:134px;top:2384px;width:370px;font-size:11px;line-height:17px;color:#a59d97}
.social{top:2439px;width:34px;height:34px;border-radius:50%}
.details{left:137px;top:2493px;font-size:11.5px;line-height:20px;color:#e9e4e0}
.copyright{left:132px;top:2572px;font-size:11px;color:#e9e4e0}
.field{background:var(--white);border:0;font-family:inherit;font-size:12px;color:#b5b5b5;padding:10px 14px}
.btn-send{left:931px;top:2585px;width:136px;height:41px;background:var(--blue);color:var(--white);font-size:13px;font-weight:600;text-align:center;line-height:41px}
</style>
</head>
<body>

<!-- top bar -->
<div class="abs topbar">
  <span class="abs booking">Need Booking</span>
  <svg class="abs phone-icon" width="26" height="26" viewBox="0 0 26 26" aria-hidden="true">
    <circle cx="13" cy="13" r="11.5" fill="none" stroke="#fff" stroke-width="1.5"/>
    <path d="M9 8.5c.8-.8 1.6-.6 2 .2l.9 1.8c.3.6.1 1.1-.4 1.5l-.6.5c.6 1.4 1.6 2.4 3 3l.5-.6c.4-.5.9-.7 1.5-.4l1.8.9c.8.4 1 1.2.2 2-1.4 1.4-3.4 1-5.6-1.1C8.2 14 7.6 10 9 8.5z" fill="#fff"/>
  </svg>
  <span class="abs phone">(206) 555-0148</span>
</div>

<!-- navigation -->
<header class="abs navbar">
  <div class="abs nav-active"></div>
  <a class="abs nav-item" style="left:519px">Home</a>
  <a class="abs nav-item" style="left:598px">How It Works</a>
  <a class="abs nav-item" style="left:715px">Massages</a>
  <a class="abs nav-item" style="left:812px">Testimonials</a>
  <a class="abs nav-item" style="left:927px">Pricing</a>
  <a class="abs nav-item" style="left:1009px">Contact us</a>
</header>
<div class="abs brand"><span class="brand-name">Kestrel Way</span></div>

<!-- hero -->
<section>
  <div class="abs hero" role="img" aria-label="Photo of a therapist's hands massaging a relaxed client's shoulder, candle in the corner"></div>
  <div class="abs hero-shade"></div>
  <h1 class="abs center hero-title">BOOK AN IN-HOME OR OFFICE <b>MASSAGE</b></h1>
  <p class="abs center hero-sub">Our therapists will release your mind<br>and body tensions</p>
  <a class="abs btn-book">BOOK NOW</a>
  <div class="abs dots"><span class="dot"></span><span class="dot on"></span><span class="dot"></span></div>
</section>

<!-- welcome -->
<section>
  <h2 class="abs center section-title welcome-title">WELCOME TO <span class="accent">KESTREL WAY MASSAGE</span></h2>
  <div class="rule" style="top:699px"></div>
  <p class="abs welcome-text">We are a male and female mobile massage team. Our names are Paul and Lina.&nbsp; Kestrel Way is a Seattle based mobile massage service. Our massage is offered to the community with a goal of facilitating balance within each individual. We specialize in integrated Pain management, and sports/medical massage therapy. Every client's first assessment is attended by our male and female massage therapist team.</p>
  <a class="abs btn-small">Read More</a>
</section>

<!-- massages -->
<section class="abs massage-band">
  <h2 class="abs center section-title" style="top:44px">OUR <span class="accent">MASSAGE</span></h2>
  <div class="rule" style="top:110px"></div>

  <div class="abs card" style="left:128px;top:143px">
    <svg class="card-icon" viewBox="0 0 88 88" aria-hidden="true">
      <circle cx="44" cy="44" r="42" fill="#fff" stroke="#0a95cc" stroke-width="2.5"/>
      <circle cx="44" cy="44" r="35" fill="none" stroke="#0a95cc" stroke-width="1"/>
      <g fill="none" stroke="#0a95cc" stroke-width="2" stroke-linecap="round">
        <path d="M26 50h36M30 50v10M58 50v10M34 44h22"/>
        <circle cx="34" cy="34" r="3.5"/>
        <path d="M42 40l8-8M50 32h8"/>
      </g>
    </svg>
    <h3>Pain Management</h3>
    <p>Praesent sed hendrerit ligula. Praesent eros turpis iaculis id gravida eu, consequat viverra odio. Phasellus ac arcu lacus. Sed at nunc feugiat.</p>
    <div class="more">Read about &#187;</div>
  </div>

  <div class="abs card" style="left:449px;top:143px">
    <svg class="card-icon" viewBox="0 0 88 88" aria-hidden="true">
      <circle cx="44" cy="44" r="42" fill="#fff" stroke="#0a95cc" stroke-width="2.5"/>
      <circle cx="44" cy="44" r="35" fill="none" stroke="#0a95cc" stroke-width="1"/>
      <g fill="none" stroke="#0a95cc" stroke-width="2" stroke-linejoin="round">
        <path d="M36 24h16l2 8-2 30H36l-2-30z"/>
        <path d="M38 36h12M38 46h12M38 56h12"/>
      </g>
    </svg>
    <h3>Sports Massage</h3>
    <p>Praesent sed hendrerit ligula. Praesent eros turpis iaculis id gravida eu, consequat viverra odio. Phasellus ac arcu lacus. Sed at nunc feugiat.</p>
    <div class="more">Read about &#187;</div>
  </div>

  <div class="abs card" style="left:769px;top:143px">
    <svg class="card-icon" viewBox="0 0 88 88" aria-hidden="true">
      <circle cx="44" cy="44" r="42" fill="#fff" stroke="#0a95cc" stroke-width="2.5"/>
      <circle cx="44" cy="44" r="35" fill="none" stroke="#0a95cc" stroke-width="1"/>
      <g fill="none" stroke="#0a95cc" stroke-width="2" stroke-linejoin="round">
        <path d="M40 22h8v8l6 6v26H34V36l6-6z"/>
        <path d="M44 44c-3 4-4 6-4 8a4 4 0 008 0c0-2-1-4-4-8z"/>
      </g>
    </svg>
    <h3>Medical Massage</h3>
    <p>Praesent sed hendrerit ligula. Praesent eros turpis iaculis id gravida eu, consequat viverra odio. Phasellus ac arcu lacus. Sed at nunc feugiat.</p>
    <div class="more">Read about &#187;</div>
  </div>
</section>

<!-- why choose us -->
<section class="abs why">
  <div class="abs why-photo" style="top:0" role="img" aria-label="Faded blue-toned photo of a client relaxing during a massage"></div>
  <h2 class="abs center section-title" style="top:55px;color:#fff">WHY CHOOS US</h2>
  <div class="rule" style="top:123px"></div>

  <div class="abs reason" style="left:132px;top:168px">
    <svg width="16" height="14" viewBox="0 0 16 14" aria-hidden="true"><path d="M1 3h14v3H1zM8 6v8" stroke="#fff" stroke-width="2" fill="none"/></svg>
    <h4>OUR PASSION...</h4>
    <p>Here at Kestrel Way, we have a great passion for Postural Resoration and how it is integrated into an individual's Massage treatment.</p>
    <div class="more">Read about &#187;</div>
  </div>
  <div class="abs reason" style="left:453px;top:168px">
    <svg width="14" height="16" viewBox="0 0 14 16" aria-hidden="true"><rect x="1" y="1" width="12" height="14" fill="#fff"/><path d="M4 5h6M4 8h6M4 11h6" stroke="#0b8dc5" stroke-width="1.3"/></svg>
    <h4>OUR EDUCATION...</h4>
    <p>Here at Kestrel Way, we have a great passion for Postural Resoration and how it is integrated into an individual's Massage treatment.</p>
    <div class="more">Read about &#187;</div>
  </div>
  <div class="abs reason" style="left:773px;top:168px">
    <svg width="14" height="16" viewBox="0 0 14 16" aria-hidden="true"><path d="M2 15L12 2M5 11c0-5 3-8 7-9-1 4-3 7-7 9z" stroke="#fff" stroke-width="1.6" fill="#fff"/></svg>
    <h4>ADVICE TO ANY MASSAGE CLIENT</h4>
    <p>Here at Kestrel Way, we have a great passion for Postural Resoration and how it is integrated into an individual's Massage treatment.</p>
    <div class="more">Read about &#187;</div>
  </div>
</section>

<!-- testimonials -->
<section>
  <h2 class="abs center section-title testi-title">CLIENT <span class="accent">TESTIMONIAL</span></h2>
  <div class="rule" style="top:1901px"></div>
  <svg class="abs" style="left:313px;top:1965px" width="16" height="26" viewBox="0 0 16 26" aria-hidden="true"><path d="M13 2L3 13l10 11" stroke="#c7ccd0" stroke-width="2" fill="none"/></svg>
  <svg class="abs" style="left:869px;top:1965px" width="16" height="26" viewBox="0 0 16 26" aria-hidden="true"><path d="M3 2l10 11L3 24" stroke="#c7ccd0" stroke-width="2" fill="none"/></svg>
  <div class="abs avatar" style="left:352px" role="img" aria-label="Client portrait"></div>
  <div class="abs avatar" style="left:456px;background:linear-gradient(160deg,#d8b99c,#8f6a4f)" role="img" aria-label="Client portrait"></div>
  <div class="abs avatar active" style="left:559px;background:linear-gradient(160deg,#b98f70,#5d4332)" role="img" aria-label="Client portrait, selected"></div>
  <div class="abs avatar" style="left:664px;background:linear-gradient(160deg,#d1a787,#7a5039)" role="img" aria-label="Client portrait"></div>
  <div class="abs avatar" style="left:769px;background:linear-gradient(160deg,#c09b80,#5a4537)" role="img" aria-label="Client portrait"></div>
  <div class="abs" style="left:560px;top:2045px;width:40px;height:1px;background:var(--line)"></div>
  <div class="abs" style="left:618px;top:2045px;width:22px;height:1px;background:var(--line)"></div>
  <svg class="abs" style="left:592px;top:2037px" width="16" height="14" viewBox="0 0 16 14" aria-hidden="true"><path d="M1 13V7c0-3 2-5 5-6v2c-2 1-2 2-2 4h2v6zM9 13V7c0-3 2-5 5-6v2c-2 1-2 2-2 4h2v6z" fill="#0a95cc"/></svg>
  <p class="abs quote-text">Lorem ipsum dolor sit amet, consectetur adipiscing elit. Nulla eu leo eu metus congue aliquet. Pellentesque id lectus volutpat ullamcorper nibh eu tempor orci. Praesent in orci neque phasellus ac lobortis ipsum Integer non felis nec diam dapibus tincidunt.</p>
  <p class="abs center quote-name">Maren J.</p>
</section>

<!-- contact -->
<section>
  <div class="abs contact" role="img" aria-label="Dark blurred photo of a massage room"></div>
  <h2 class="abs center section-title contact-title">CONTACT US</h2>
  <div class="rule"></div>
  <h3 class="abs touch" style="font-weight:400">Get in touch with us</h3>
  <p class="abs touch-text">Lorem Ipsum is simply dummy text of the printing and typesetting industry. Lorem Ipsum has been the industry's</p>
  <div class="abs social" style="left:129px;background:#3b5a9a" aria-label="Social profile"></div>
  <div class="abs social" style="left:174px;background:#2aa3e6" aria-label="Social profile"></div>
  <div class="abs social" style="left:219px;background:#dd4b39" aria-label="Social profile"></div>
  <p class="abs details">Neque porro quisquam est, qui dolorem ipsum quia dolor sit amet<br>(206) 555-0148<br>info@kestrelwaymail.net</p>
  <p class="abs copyright">&copy; 2015 <span class="accent">kestrelwaymassage.com</span>. All rights reserved.</p>

  <div class="abs field" style="left:612px;top:2357px;width:217px;height:36px">Name</div>
  <div class="abs field" style="left:850px;top:2357px;width:217px;height:36px">Email</div>
  <div class="abs field" style="left:612px;top:2419px;width:455px;height:142px">Message</div>
  <a class="abs btn-send">SEND</a>
</section>

</body>
</html>
```